KLV Plant Services

We are a heavy diesel mechanical business with additional air con certificates, remapping engine rebuilt

Contact Information for Business Card

Company Name, Director Name, Managing Director, Contact details, email and website

Font styles to use
Serif
Script

```html
<!DOCTYPE html>
<html lang="en">
<head>
<meta charset="utf-8">
<title>KLV Plant Services – Business Card</title>
<link rel="stylesheet" href="https://fonts.googleapis.com/css2?family=Lato:wght@400;700&display=swap">
<style>
  :root {
    --page-bg: #e9e9eb;
    --card-bg: #ffffff;
    --card-edge: #111111;
    --navy: #2b2a7c;
    --ink: #1d1d1d;
    --text-grey: #4a4a4a;
    --rule: #9a9a9a;
  }
  * { box-sizing: border-box; margin: 0; padding: 0; }
  html, body {
    width: 1200px;
    height: 900px;
    overflow: hidden;
    background: var(--page-bg);
    font-family: "Lato", sans-serif;
  }
  .sheet {
    position: relative;
    width: 1200px;
    height: 900px;
  }
  .card {
    position: absolute;
    width: 700px;
    height: 400px;
    background: linear-gradient(135deg, #ffffff 0%, #f4f4f4 100%);
    border-bottom: 6px solid var(--card-edge);
    box-shadow: 0 10px 24px rgba(0,0,0,0.18);
    overflow: hidden;
  }
  .card--front { left: 250px; top: 40px; }
  .card--back  { left: 250px; top: 470px; }

  .brand {
    position: absolute;
    display: flex;
    align-items: center;
    gap: 14px;
  }
  .brand__dot {
    width: 22px;
    height: 22px;
    border-radius: 50%;
    background: var(--navy);
    flex: none;
  }
  .brand__name {
    color: var(--navy);
    font-weight: 700;
    font-size: 30px;
    line-height: 1.05;
    letter-spacing: 0.01em;
  }
  .card--front .brand { left: 370px; top: 120px; }
  .card--back  .brand { left: 390px; top: 70px; }

  .divider {
    position: absolute;
    left: 290px;
    right: 40px;
    top: 232px;
    height: 1px;
    background: var(--rule);
  }

  .person {
    position: absolute;
    left: 60px;
    top: 212px;
  }
  .person__name {
    color: var(--navy);
    font-weight: 700;
    font-size: 24px;
    letter-spacing: 0.03em;
    text-transform: uppercase;
  }
  .person__role {
    color: var(--ink);
    font-size: 16px;
    margin-top: 2px;
    padding-left: 28px;
  }

  .contacts {
    position: absolute;
    left: 60px;
    top: 290px;
    list-style: none;
  }
  .contacts__item {
    display: flex;
    align-items: center;
    gap: 10px;
    color: var(--text-grey);
    font-size: 16px;
    line-height: 24px;
  }
  .contacts__icon {
    width: 14px;
    height: 14px;
    fill: none;
    stroke: var(--navy);
    stroke-width: 2;
    flex: none;
  }
  .contacts__icon--solid { fill: var(--navy); stroke: none; }
</style>
</head>
<body>
<main class="sheet">

  <section class="card card--front" aria-label="Business card front">
    <div class="brand">
      <span class="brand__dot"></span>
      <span class="brand__name">KLV<br>Plant Services</span>
    </div>
  </section>

  <section class="card card--back" aria-label="Business card back">
    <div class="brand">
      <span class="brand__dot"></span>
      <span class="brand__name">KLV<br>Plant Services</span>
    </div>

    <div class="divider"></div>

    <div class="person">
      <p class="person__name">Dean Marlow</p>
      <p class="person__role">Managing Director</p>
    </div>

    <ul class="contacts">
      <li class="contacts__item">
        <svg class="contacts__icon contacts__icon--solid" viewBox="0 0 24 24" aria-hidden="true"><path d="M6.6 10.8a15.1 15.1 0 0 0 6.6 6.6l2.2-2.2a1 1 0 0 1 1-.25 11.4 11.4 0 0 0 3.6.57 1 1 0 0 1 1 1V20a1 1 0 0 1-1 1A17 17 0 0 1 3 4a1 1 0 0 1 1-1h3.5a1 1 0 0 1 1 1c0 1.25.2 2.45.57 3.6a1 1 0 0 1-.25 1z"/></svg>
        0400 123 456
      </li>
      <li class="contacts__item">
        <svg class="contacts__icon" viewBox="0 0 24 24" aria-hidden="true"><rect x="2" y="5" width="20" height="14"/><path d="M2 5l10 8 10-8"/></svg>
        admin@klvplantservices.net
      </li>
      <li class="contacts__item">
        <svg class="contacts__icon" viewBox="0 0 24 24" aria-hidden="true"><circle cx="12" cy="12" r="10"/><path d="M2 12h20M12 2c3 3 3 17 0 20M12 2c-3 3-3 17 0 20"/></svg>
        www.klvplantservices.net
      </li>
      <li class="contacts__item">
        <svg class="contacts__icon contacts__icon--solid" viewBox="0 0 24 24" aria-hidden="true"><path d="M12 2a7 7 0 0 0-7 7c0 5 7 13 7 13s7-8 7-13a7 7 0 0 0-7-7zm0 9.5A2.5 2.5 0 1 1 12 6.5a2.5 2.5 0 0 1 0 5z"/></svg>
        48 Harlow Street, Ridgeview, WA 6000, Australia
      </li>
    </ul>
  </section>

</main>
</body>
</html>
```